Pinecrest Harbor Foundation Web Design

The design we need is for a WordPress blog that will be our content platform. We are a registered 501(c)3 non-profit that focuses on financially supporting the treatment of cancer patients that have been told they have no hope and there is nothing the conventional medical system can do for them. Through this wesbite we want to both rasie awareness about the treatment options plus, raise funds for treating patients. The two primary target audiences of the site are...

1. Terminally ill patients and their families to let them know that there is an option other then hospice and that we are hear to support that option.

2. People looking to help donate to a worthwhile cause that resonates with them.

The website is https://pinecrestharborfoundation.org/

See attached logo designs!!!

Target Market(s)

Cancer patients and their families

Industry/Entity Type

Foundation

Font styles to use
Sans Serif

Colors
ffffff
fbed22

Requirements
Must have
• I like this look of this site. It is clean, simple, helpful, soft. I like the flow of the pages.
• http://www.meadowsforcalm.org/
• I like the design and flow but NOT the color or boldness
• https://tvbn-youth.org/
• I like this style for a donation page.
• https://www.tumorstudyhub.org/we-are-tsh/join-the-cause/donations/one-time-donation
• with the addition of a Would you like your employer to match? button.
Nice to have
• White black and gold - but soft
• Even possibly grayscale like the site I like.

```html
<!DOCTYPE html>
<html lang="en">
<head>
<meta charset="utf-8">
<title>Pinecrest Harbor Foundation</title>
<link href="https://fonts.googleapis.com/css2?family=Questrial&display=swap" rel="stylesheet">
<style>
:root{
  --pink:#e8a4a6;
  --pink-soft:#f2c4c5;
  --pink-box:rgba(229,160,163,.92);
  --ink:#333333;
  --ink-soft:#555555;
  --line:#d9d9d9;
  --grey-bg:#efefef;
  --band:#a8adbf;
  --white:#ffffff;
}
*{box-sizing:border-box;margin:0;padding:0}
html,body{width:1200px;height:2848px;overflow:hidden;background:var(--white)}
body{position:relative;font-family:"Questrial",Arial,sans-serif;color:var(--ink)}
.abs{position:absolute}
.top-rule{left:0;top:0;width:1200px;height:6px;background:var(--pink)}
.header{left:0;top:6px;width:1200px;height:102px;border-bottom:1px solid #eee}
.brand{left:161px;top:34px;color:var(--pink);font-size:22px;line-height:28px;letter-spacing:1px;text-transform:uppercase}
.call{left:783px;top:24px;font-size:15px;letter-spacing:.5px}
.call span{color:var(--pink)}
.donate-btn{left:955px;top:17px;width:84px;height:33px;border:1.5px solid var(--pink);color:var(--pink);font-size:12px;text-align:center;line-height:30px;letter-spacing:1px}
.nav{top:74px;font-size:14px}
.nav.active{color:var(--pink)}
.hero{left:0;top:108px;width:1200px;height:481px;background:linear-gradient(100deg,#f4e7e3 0%,#f2d9d4 40%,#ecd3cf 70%,#f3e5e1 100%)}
.hero-box{left:161px;top:186px;width:323px;height:327px;background:var(--pink-box);color:var(--white);padding:54px 38px}
.hero-box h1{font-weight:400;font-size:27px;line-height:38px}
.hero-box p{font-size:12px;line-height:21px;margin-top:18px;opacity:.95}
.btn-outline-white{display:inline-block;margin-top:24px;width:152px;height:42px;border:1.5px solid var(--white);border-radius:21px;text-align:center;line-height:39px;font-size:12px;letter-spacing:1px}
.arrow{width:32px;height:32px;border-radius:50%;border:1.5px solid var(--white);top:332px}
.dots{left:566px;top:543px;display:flex;gap:6px}
.dots i{width:12px;height:12px;border-radius:50%;background:var(--white);display:block}
.dots i.on{background:#2d6a3e}
.section-title{left:0;width:1200px;text-align:center;font-size:25px;font-weight:400}
.welcome-title{top:626px;color:var(--pink)}
.card-img{top:689px;width:274px;height:175px}
.card{top:880px;width:274px;text-align:center}
.card h3{font-weight:400;color:var(--pink);font-size:18px}
.card p{font-size:12.5px;line-height:19px;margin-top:12px}
.btn-line{display:inline-block;margin-top:14px;width:108px;height:35px;border:1px solid #777;font-size:11px;line-height:33px;letter-spacing:1px}
.registered{left:0;top:1113px;width:1200px;height:397px;background:linear-gradient(90deg,#a9aec0 0%,#b2b6c6 50%,#c9cad5 100%)}
.registered-text{left:163px;top:1188px;width:360px;color:var(--white)}
.registered-text h2{font-weight:400;font-size:23px;line-height:33px}
.registered-text p{font-size:12px;line-height:24px;margin-top:22px}
.btn-fill{display:block;margin-top:24px;margin-left:-3px;width:191px;height:47px;background:var(--pink);color:var(--white);font-size:14px;line-height:47px;text-align:center;letter-spacing:1px}
.what-title{top:1547px;color:var(--ink)}
.ring{top:1616px;width:152px;height:152px;border-radius:50%;border:4px solid #555;display:flex;align-items:center;justify-content:center}
.ring-inner{width:122px;height:122px;border-radius:50%;border:1.5px solid #999;display:flex;align-items:center;justify-content:center}
.service{top:1776px;width:300px;text-align:center}
.service h3{font-weight:400;color:var(--pink);font-size:17px}
.service p{font-size:12.5px;line-height:24px;margin-top:12px}
.who{left:0;top:1952px;width:1200px;height:489px;background:var(--grey-bg)}
.who-box{left:161px;top:2036px;width:337px;height:337px;background:var(--white);padding:30px 25px}
.who-box h2{font-weight:400;font-size:26px}
.who-box .lead{color:var(--pink);font-size:15.5px;line-height:25px;margin-top:20px}
.who-box p{font-size:12.5px;line-height:22px;margin-top:12px}
.who-box .more{color:var(--pink);font-size:14px;margin-top:18px;display:block}
.who-img{left:498px;top:2036px;width:541px;height:337px;background:linear-gradient(90deg,#e6e3df 0%,#d8e3e2 40%,#9fb7cc 80%,#5e7ea4 100%)}
.play{left:731px;top:2167px;width:76px;height:76px;border-radius:50%;border:3px solid var(--white)}
.call-band{left:0;top:2441px;width:1200px;height:100px;background:linear-gradient(90deg,#eeaaa9,#f2bbb9 50%,#eeaaa9);color:var(--white);font-size:23px;display:flex;align-items:center;justify-content:center;gap:14px}
.foot-col{top:2578px;font-size:12px}
.foot-col h4{font-weight:400;font-size:13px;letter-spacing:.5px;text-transform:uppercase;margin-bottom:18px}
.foot-col li{list-style:none;line-height:26px;font-size:12px}
.social{display:flex;gap:14px;margin-bottom:26px}
.social i{display:block;width:18px;height:18px;border-radius:50%;background:var(--ink)}
.foot-rule{left:161px;top:2777px;width:878px;height:1px;background:#e6e6e6}
.copy{left:0;top:2799px;width:1200px;text-align:center;font-size:12px}
</style>
</head>
<body>
<div class="abs top-rule"></div>
<header class="abs header">
  <div class="abs brand" style="top:28px">Pinecrest Harbor<br>Foundation</div>
</header>
<div class="abs call">CALL US: <span>555-018-2470</span></div>
<div class="abs donate-btn">DONATE</div>
<div class="abs nav active" style="left:531px">Home</div>
<div class="abs nav" style="left:613px">About us</div>
<div class="abs nav" style="left:707px">Who we are</div>
<div class="abs nav" style="left:824px">Funds</div>
<div class="abs nav" style="left:900px">Blog</div>
<div class="abs nav" style="left:972px">Contact us</div>

<section class="abs hero" role="img" aria-label="Smiling women wearing pink awareness ribbons"></section>
<div class="abs hero-box">
  <h1>Pinecrest Harbor Foundation</h1>
  <p>Sed ut perspiciatis unde omnis iste nit orsit voluptatem accusantium doloreue laudantium totam rem.</p>
  <span class="btn-outline-white">FIND OUT MORE</span>
</div>
<svg class="abs arrow" style="left:38px" viewBox="0 0 32 32"><path d="M18 10l-6 6 6 6" fill="none" stroke="#fff" stroke-width="2"/></svg>
<svg class="abs arrow" style="left:1128px" viewBox="0 0 32 32"><path d="M14 10l6 6-6 6" fill="none" stroke="#fff" stroke-width="2"/></svg>
<div class="abs dots"><i></i><i></i><i class="on"></i><i></i></div>

<h2 class="abs section-title welcome-title">Welcome to Pinecrest Harbor Foundation</h2>
<div class="abs card-img" style="left:161px;background:linear-gradient(135deg,#f1ece8,#d9cfc9)" role="img" aria-label="Patient resting in a bright hospital room"></div>
<div class="abs card-img" style="left:463px;background:linear-gradient(135deg,#f7e3e6,#eebfc8)" role="img" aria-label="Open hands holding a pink ribbon"></div>
<div class="abs card-img" style="left:765px;background:linear-gradient(135deg,#cfdde6,#6c8aa6)" role="img" aria-label="Patient in a headscarf sitting by a window"></div>
<div class="abs card" style="left:161px"><h3>Finibus Bonorum</h3><p>Sed ut perspiciatis unde omnissitup tem accusantium doloremqlque uotem aperiam, eaqueuaeab illo inventcus atium doloremqloue uotam ror.</p><span class="btn-line">READ MORE</span></div>
<div class="abs card" style="left:463px"><h3>Finibus Bonorum</h3><p>Sed ut perspiciatis unde omnissitup tem accusantium doloremqlque uotem aperiam, eaqueuaeab illo inventcus atium doloremqloue uotam ror.</p><span class="btn-line">READ MORE</span></div>
<div class="abs card" style="left:765px"><h3>Finibus Bonorum</h3><p>Sed ut perspiciatis unde omnissitup tem accusantium doloremqlque uotem aperiam, eaqueuaeab illo inventcus atium doloremqloue uotam ror.</p><span class="btn-line">READ MORE</span></div>

<section class="abs registered" role="img" aria-label="Smiling older woman in a headscarf with a younger woman"></section>
<div class="abs registered-text">
  <h2>We Are Registered 501(c)3<br>non-profit organisations</h2>
  <p>Sed ut perspiciatis unde omnis iste natus errorsit volup tatecusdoloeut perspiciatis unde omniste natussit voluptatemcustum doloremque launtum</p>
  <span class="btn-fill">REGISTERED HERE</span>
</div>

<h2 class="abs section-title what-title">What We Do</h2>
<div class="abs ring" style="left:213px"><div class="ring-inner">
  <svg width="60" height="54" viewBox="0 0 60 54"><path d="M30 50C10 36 3 26 3 16 3 8 9 3 16 3c6 0 11 4 14 9 3-5 8-9 14-9 7 0 13 5 13 13 0 10-7 20-27 34z" fill="none" stroke="#e8a4a6" stroke-width="3.5"/></svg>
</div></div>
<div class="abs ring" style="left:522px"><div class="ring-inner">
  <svg width="64" height="64" viewBox="0 0 64 64" fill="none" stroke="#e8a4a6" stroke-width="3"><circle cx="26" cy="38" r="12"/><path d="M26 32v12M23 35h6M23 41h6"/><path d="M34 30l16-16a4 4 0 016 6L42 34"/><path d="M14 54h20l12-10"/></svg>
</div></div>
<div class="abs ring" style="left:834px"><div class="ring-inner">
  <svg width="60" height="60" viewBox="0 0 60 60"><circle cx="30" cy="22" r="13" fill="#e8a4a6"/><path d="M8 56c2-14 11-20 22-20s20 6 22 20z" fill="#e8a4a6"/></svg>
</div></div>
<div class="abs service" style="left:139px"><h3>Donate</h3><p>Sed ut perspiciatis unde ovoloreglu ptatem accusantium dolorelor mqloue udantium, totam rem aperia eu.</p></div>
<div class="abs service" style="left:448px"><h3>Raise Funds</h3><p>Sed ut perspiciatis unde ovoloreglu ptatem accusantium dolorelor mqloue udantium, totam rem aperia eu.</p></div>
<div class="abs service" style="left:760px"><h3>Patients</h3><p>Sed ut perspiciatis unde ovoloreglu ptatem accusantium dolorelor mqloue udantium, totam rem aperia eu.</p></div>

<section class="abs who"></section>
<div class="abs who-box">
  <h2>Who We Are</h2>
  <div class="lead">Raise awareness about the treatment options plus, raise funds for treating patients</div>
  <p>Sed ut perspiciatis unde omnissit voluptat em accusantium doloremqlque udant lorium, totam rem aperiam, eaqueuaeab illo loreinv entore veritatis etuam rem aperiam.</p>
  <span class="more">Read More</span>
</div>
<div class="abs who-img" role="img" aria-label="Young patient with a teddy bear beside a nurse, video preview"></div>
<svg class="abs play" viewBox="0 0 76 76"><path d="M30 22l24 16-24 16z" fill="#fff"/></svg>

<div class="abs call-band">
  <svg width="26" height="26" viewBox="0 0 24 24"><path d="M6.6 10.8a15 15 0 006.6 6.6l2.2-2.2c.3-.3.7-.4 1-.2 1.1.4 2.3.6 3.6.6.6 0 1 .4 1 1V20c0 .6-.4 1-1 1A17 17 0 013 4c0-.6.4-1 1-1h3.5c.6 0 1 .4 1 1 0 1.3.2 2.5.6 3.6.1.3 0 .7-.2 1z" fill="none" stroke="#fff" stroke-width="1.6"/></svg>
  <span>Call us on 555 019 6621</span>
</div>

<div class="abs foot-col" style="left:161px"><h4>About</h4><ul><li>Refer</li><li>Careers</li><li>News</li><li>Non Profit</li><li>Contact</li></ul></div>
<div class="abs foot-col" style="left:296px"><h4>Information</h4><ul><li>Target patients</li><li>Organisation</li><li>Sed uerspiciatiem</li><li>Comnisteatusit</li><li>Perspiciatis unde</li></ul></div>
<div class="abs foot-col" style="left:513px"><h4>Who We Are</h4><ul><li>Sed utespiciatis</li><li>Donate</li><li>Perspiciatis unde</li><li>Sed uerspiciatiem</li><li>Comnisteatusit</li></ul></div>
<div class="abs foot-col" style="left:708px"><h4>Connect</h4><div class="social"><i></i><i></i><i></i><i></i></div><h4 style="margin-bottom:8px">Policies</h4><ul><li>Privacy</li><li>Complaint and Feedback</li></ul></div>
<div class="abs foot-col" style="left:927px"><h4>Other Links</h4><ul><li>Sed utespiciatis</li><li>Healthcare</li><li>Perspiciatis unde</li><li>Sed uerspiciatiem</li><li>Comnisteatusit</li></ul></div>
<div class="abs foot-rule"></div>
<div class="abs copy">© 2017 Pinecrest Harbor Foundation. Privacy Policy &nbsp;|&nbsp; Terms of Use &nbsp;|&nbsp; Contact</div>
</body>
</html>
```